Tidewater Motion Bodywork needs a Website

I'm a Massage Practitioner wanting a website for promotion and bookings with a Blog area and inplementation to my facebook page https://www.pagewall-social.com/TidewaterMotionBodywork , my setmore Booking page http://my.slotkeeper.net/bookingpage/a73e2d41-5b6c-4e82-9f07-c18d25e6b3a0 and my PayPal account to make payments.
The Venues changes from time to time. In October 2015 it will be the Coralspan Endurance Worldchampionship in Kona Hawaii

Target Market(s)

Sports People participating in targeted Events

Industry/Entity Type

Massage

Number of Pages Required

5+ page

Font styles to use
Other font styles liked:
• Verdana

Colors
3176b5
5db8de
ec1f27
ffffff

Requirements
Must have
• An About page including which events (in this case Coralspan Endurance World Championship in Kona, Hawaii in October 2015)
• A page with the Techniques I use
• Inplementation of my Setmore Booking Page http://my.slotkeeper.net/bookingpage/a73e2d41-5b6c-4e82-9f07-c18d25e6b3a0
• Implementation of my Facebook Page https://www.pagewall-social.com/TidewaterMotionBodywork
Nice to have
• Would be great to have a Blog with Pictures Upload ability
• Tried to upload Pictures but it always says that it is a non supported file type, so contact me to send you those informations. More informations about me to be found on http://wellroot.com.au/about-us/meet-the-team/jon-harlow-pike---massage-therapist.html

```html
<!DOCTYPE html>
<html lang="en">
<head>
<meta charset="utf-8">
<title>Tidewater Motion Bodywork</title>
<link rel="stylesheet" href="https://fonts.googleapis.com/css2?family=Cabin:wght@400;500;700&family=Roboto:ital,wght@0,300;0,400;0,500;1,400&display=swap">
<style>
:root{
  --blue-dark:#3176b5;
  --blue-light:#5db8de;
  --red:#ec1f27;
  --white:#ffffff;
  --text:#666a70;
  --head:"Cabin",Verdana,sans-serif;
  --body:"Roboto",Verdana,sans-serif;
}
*{margin:0;padding:0;box-sizing:border-box}
html,body{width:1200px;height:2169px;overflow:hidden;background:var(--white)}
body{position:relative;font-family:var(--body);color:var(--text)}
.abs{position:absolute}
a{color:inherit;text-decoration:none}

/* header */
.top-rule{left:0;top:0;width:1200px;height:5px;background:var(--blue-light)}
.book-tab{left:794px;top:4px;width:332px;height:36px;background:var(--blue-light);color:#1d4f7e;
  font:500 12px var(--body);display:flex;align-items:center;justify-content:center;gap:6px;letter-spacing:.3px}
.book-tab strong{color:var(--white);font:500 21px var(--head);letter-spacing:.5px}
.brand{left:77px;top:34px;display:flex;align-items:center;gap:12px}
.brand-dot{width:74px;height:66px;border-radius:50%;background:var(--blue-light)}
.brand-name{font:400 16px/19px var(--head);color:var(--red);width:120px}
.main-nav{left:536px;top:82px;width:590px;display:flex;justify-content:space-between}
.main-nav a{font:500 12px var(--body);color:#3a3a3a;letter-spacing:.3px;padding:0 0 10px;text-transform:uppercase;white-space:nowrap}
.main-nav a.active{color:var(--red);border-bottom:3px solid var(--red);padding:0 20px 8px}

/* hero */
.hero{left:75px;top:114px;width:1051px;height:429px;border:3px solid #d6d6d6;
  background:linear-gradient(100deg,#5b5a4c 0%,#8c8a78 30%,#b8b4a4 55%,#d8d4c6 80%,#c7c2b4 100%)}
.hero-title{left:75px;top:232px;width:1051px;text-align:center;color:var(--white);
  text-shadow:0 2px 6px rgba(0,0,0,.55)}
.hero-title .l1{display:block;font:700 58px/58px var(--head);letter-spacing:1px}
.hero-title .l2{display:block;font:400 56px/62px var(--head)}
.btn{background:var(--red);color:var(--white);font:500 12px var(--body);letter-spacing:.4px;
  display:flex;align-items:center;justify-content:center;text-transform:uppercase;box-shadow:0 2px 0 rgba(0,0,0,.15)}
.hero-btn{left:511px;top:381px;width:179px;height:31px}
.hero-dots{left:557px;top:501px;display:flex;gap:8px}
.hero-dots span{width:14px;height:14px;border-radius:50%;background:#4b4b4b}
.hero-dots span.on{background:var(--blue-dark)}

/* welcome */
.welcome-title{left:0;top:578px;width:1200px;text-align:center;font:400 21px var(--head);color:var(--blue-dark);letter-spacing:.5px}
.welcome-text{left:165px;top:623px;width:870px;text-align:center;font:300 14px/22px var(--body);color:#5f6368}

/* bands */
.band{left:0;width:1200px}
.section-title{font:400 22px var(--head);color:var(--white);letter-spacing:.6px;text-transform:uppercase}

/* services */
.services-title{left:77px;top:818px}
.service{top:863px;width:218px}
.service-photo{width:218px;height:145px;border:2px solid #8ab2c9}
.service h3{margin-top:17px;font:700 15px/21px var(--body);color:var(--red);text-transform:uppercase;letter-spacing:.2px}
.service p{margin-top:8px;width:205px;font:300 12px/21px var(--body);color:#eaf6fc}

/* pricing */
.pricing{left:821px;top:797px;width:305px;height:346px;background:var(--blue-dark);
  clip-path:polygon(0 0,100% 4.5%,100% 100%,0 100%);padding:30px 20px 0 19px;color:var(--white)}
.panel-title{font:400 22px var(--head);color:var(--white);letter-spacing:.6px;text-transform:uppercase}
.price-row{display:flex;justify-content:space-between;align-items:flex-start;border-bottom:1px dashed #7fb0df;padding:12px 0}
.price-row:last-of-type{border-bottom:none}
.price-row .name{font:400 13px/19px var(--body);width:200px}
.price-row .dur{display:block;font:italic 400 12px/22px var(--body);color:#dbe8f5}
.price-row .amt{font:400 14px/19px var(--body)}
.price-row.tall .amt{margin-top:19px}
.pricing .btn{width:178px;height:31px;margin-top:6px}

/* staff */
.staff-title{left:75px;top:1206px;font:400 22px var(--head);color:var(--blue-dark);letter-spacing:.6px;text-transform:uppercase}
.staff-photo{left:77px;top:1255px;width:238px;height:214px;border:3px solid #e1e1e1;
  background:linear-gradient(120deg,#cfd3d0 0%,#b3a39a 45%,#a8424a 70%,#e8e4dc 100%)}
.staff-name{left:343px;top:1252px;font:400 17px var(--body);color:var(--red)}
.staff-role{left:343px;top:1280px;width:380px;font:400 13px/18px var(--body);color:var(--blue-dark)}
.staff-bio{left:343px;top:1320px;width:430px;font:300 12px/21px var(--body);color:#5f6368}
.staff-btn{left:343px;top:1441px;width:140px;height:30px}

/* testimonials */
.testimonials{left:821px;top:1213px;width:305px;height:322px;background:var(--blue-dark);
  clip-path:polygon(0 0,100% 0,100% 100%,0 95.5%);padding:24px 22px 0 22px;color:var(--white)}
.quote{margin-top:20px;display:flex;gap:8px;font:italic 400 12px/21px var(--body);color:#dfeaf6}
.quote-mark{font:700 26px/20px var(--head);color:#7fb0df}
.author{margin-top:22px;display:flex;align-items:center;gap:20px}
.author-avatar{width:56px;height:56px;background:var(--white);border-radius:3px}
.author-name{font:italic 500 13px var(--body)}
.author-loc{font:italic 400 11px/20px var(--body);color:#c8daf0}
.testimonials .btn{width:86px;height:30px;margin:20px 0 0 auto}

/* gallery */
.gallery-title{left:77px;top:1605px}
.gallery-arrows{left:1090px;top:1606px;display:flex;gap:14px}
.gallery-item{top:1660px;width:241px;height:145px;border:2px solid #8ab2c9}

/* footer */
.footer{left:0;top:1843px;width:1200px;height:326px;background:var(--red)}
.foot-col{top:1875px;color:var(--white)}
.foot-col h4{font:700 13px var(--body);letter-spacing:.5px;text-transform:uppercase;margin-bottom:9px}
.foot-col li{list-style:none;font:300 12px/25px var(--body);color:#fde2e2}
.foot-col p{font:300 12px/25px var(--body);color:#fde2e2}
.foot-divider{top:1877px;width:1px;height:188px;background:#f36a6e}
.hours{display:grid;grid-template-columns:66px 90px;font:300 12px/25px var(--body);color:#fde2e2}
.footer-strip{left:0;top:2089px;width:1200px;height:80px}
.copyright{left:77px;top:2132px;font:300 11px var(--body);color:#eaf6fc}
.social{left:960px;top:2122px;display:flex;gap:7px}
.social span{width:27px;height:27px;border:1px solid #2c5d8e;background:var(--blue-dark);border-radius:3px}
</style>
</head>
<body>

<!-- header -->
<div class="abs top-rule"></div>
<a class="abs book-tab" href="#booking">BOOK AN APPOINTMENT: <strong>+61455012874</strong></a>
<div class="abs brand">
  <span class="brand-dot"></span>
  <span class="brand-name">Tidewater Motion Bodywork</span>
</div>
<nav class="abs main-nav">
  <a class="active" href="#">Home</a>
  <a href="#">About Us</a>
  <a href="#">Services</a>
  <a href="#">Pricing</a>
  <a href="#">Staff Members</a>
  <a href="#">Contact Us</a>
</nav>

<!-- hero -->
<div class="abs hero" role="img" aria-label="Therapist in a red polo massaging an athlete's leg on a treatment table, towel shelves behind"></div>
<h1 class="abs hero-title"><span class="l1">WELCOME TO</span><span class="l2">Tidewater Motion Bodywork</span></h1>
<a class="abs btn hero-btn" href="#booking">Booking Appointment</a>
<div class="abs hero-dots"><span class="on"></span><span class="on"></span><span></span><span></span></div>

<!-- welcome -->
<h2 class="abs welcome-title">WELCOME TO OUR WEBSITE</h2>
<p class="abs welcome-text">Jon turned his passion for sport into a passion for helping athletes. As a Massage Therapist he helps athletes to perform optimally and recover faster from training and racing. Jon is trained in Swedish, Remedial &amp; Sports Massage, Active Soft Tissue Work, DEEPLINE Myofascial Release, Vessel Release Technique, Dry Needeling and Lymphatic Drainage.</p>

<!-- services band -->
<svg class="abs band" style="top:719px" width="1200" height="453" viewBox="0 0 1200 453" aria-hidden="true">
  <polygon points="0,0 1200,55 1200,453 0,453" fill="var(--blue-light)"/>
</svg>
<h2 class="abs section-title services-title">Our Services</h2>

<div class="abs service" style="left:77px">
  <div class="service-photo" role="img" aria-label="Therapist working on an athlete lying on the floor" style="background:linear-gradient(135deg,#6e6a58,#4b463a 60%,#8a7f66)"></div>
  <h3>Sport Deep Tissue Massage</h3>
  <p>Duis aute irure dolor in reprehenderit in voluptate velit esse cillum dolore euugiat nulla pariatur.</p>
</div>
<div class="abs service" style="left:318px">
  <div class="service-photo" role="img" aria-label="Hands pressing into the muscles of a back" style="background:linear-gradient(135deg,#9a9792,#c9a58c 55%,#8f6a52)"></div>
  <h3>Myofascial Release</h3>
  <p>Duis aute irure dolor in reprehenderit in voluptate velit esse cillum dolore euugiat nulla pariatur.</p>
</div>
<div class="abs service" style="left:562px">
  <div class="service-photo" role="img" aria-label="Therapist treating a client on a table in the clinic" style="background:linear-gradient(135deg,#5c5a4d,#a89a86 50%,#d2cbbd)"></div>
  <h3>Sport Deep Tissue with Active Soft Tissue Work</h3>
  <p>Duis aute irure dolor in reprehenderit in voluptate velit esse cillum dolore euugiat nulla pariatur.</p>
</div>

<section class="abs pricing">
  <h2 class="panel-title">Pricing</h2>
  <div style="margin-top:12px">
    <div class="price-row"><span class="name">Sport Deep Tissue Massage<span class="dur">60 Mins</span></span><span class="amt">$100</span></div>
    <div class="price-row"><span class="name">Myofascial Release<span class="dur">60 Mins</span></span><span class="amt">$120</span></div>
    <div class="price-row tall"><span class="name">Sport Deep Tissue with Active Soft Tissue Work<span class="dur">60 Mins</span></span><span class="amt">$100</span></div>
  </div>
  <a class="btn" href="#booking">Booking Appointment</a>
</section>

<!-- staff -->
<h2 class="abs staff-title">Our Staff Member</h2>
<div class="abs staff-photo" role="img" aria-label="Therapist and a colleague sitting together in matching red polos"></div>
<h3 class="abs staff-name">Jon Harlow-Pike</h3>
<p class="abs staff-role">Senior Massage and DEEPLINE Myofascial Therapist, Vessel Release Technique Practitioner</p>
<p class="abs staff-bio">Jon turned his passion for sport into a passion for helping athletes. As a Massage Therapist he helps athletes to perform optimally and recover faster from training and racing. Jon is trained in Swedish, Remedial &amp; Sports Massage, Active Glide Technique (AGT), DEEPLINE Myofascial Release, Vessel Release Technique, Dry Needeling and Lymphatic Drainage.</p>
<a class="abs btn staff-btn" href="#">Read More About</a>

<section class="abs testimonials">
  <h2 class="panel-title">Testimonials</h2>
  <div class="quote"><span class="quote-mark">&ldquo;</span><p>Aliquam molestie, mi et imperdiet euismod, dui purus auctor tellus, et interdum lacus lectus et ante. Sed accumsan sollicitudin sapien, sit amet adipiscing turpis gravida ac....</p></div>
  <div class="author">
    <span class="author-avatar"></span>
    <div><div class="author-name">Name Heading</div><div class="author-loc">Location</div></div>
  </div>
  <a class="btn" href="#">Read All</a>
</section>

<!-- gallery band -->
<svg class="abs band" style="top:1504px" width="1200" height="339" viewBox="0 0 1200 339" aria-hidden="true">
  <polygon points="0,0 1200,50 1200,339 0,339" fill="var(--blue-light)"/>
</svg>
<h2 class="abs section-title gallery-title">Photo Gallery</h2>
<div class="abs gallery-arrows">
  <svg width="12" height="20" viewBox="0 0 12 20" aria-hidden="true"><polyline points="10,2 2,10 10,18" fill="none" stroke="#fff" stroke-width="2"/></svg>
  <svg width="12" height="20" viewBox="0 0 12 20" aria-hidden="true"><polyline points="2,2 10,10 2,18" fill="none" stroke="#fff" stroke-width="2"/></svg>
</div>
<div class="abs gallery-item" style="left:77px;background:linear-gradient(135deg,#cfd5d8,#4d78a8 45%,#c8c0b4)" role="img" aria-label="Therapist in blue working on a client's shoulder"></div>
<div class="abs gallery-item" style="left:346px;background:linear-gradient(135deg,#6e6b5a,#b34a48 50%,#d9d5c6)" role="img" aria-label="Therapist treating a client's back on a table"></div>
<div class="abs gallery-item" style="left:616px;background:linear-gradient(135deg,#b08a4a,#4a3a2c 50%,#8c7a58)" role="img" aria-label="Athlete receiving leg treatment on the floor"></div>
<div class="abs gallery-item" style="left:885px;background:linear-gradient(135deg,#e0ddd4,#6d6a62 50%,#bdb6a8)" role="img" aria-label="Therapist stretching an athlete on a massage table"></div>

<!-- footer -->
<footer class="abs footer"></footer>
<div class="abs foot-col" style="left:77px">
  <h4>Quick Links</h4>
  <ul><li>Home</li><li>About us</li><li>Services</li><li>Pricing</li><li>Staff Members</li><li>Contact Us</li></ul>
</div>
<div class="abs foot-divider" style="left:217px"></div>
<div class="abs foot-col" style="left:255px;width:210px">
  <h4>Services</h4>
  <ul><li>Sport Deep Tissue Massage</li><li>Myofascial Release</li><li style="line-height:18px;padding-top:4px">Sport Deep Tissue with Active Soft Tissue Work</li></ul>
</div>
<div class="abs foot-divider" style="left:492px"></div>
<div class="abs foot-col" style="left:524px;width:260px">
  <h4>Location</h4>
  <p>Lantern Cove House 12-4410 Reefline Drive,<br>Saltmere Bay, HI 96799</p>
  <h4 style="margin-top:14px">Contact Info</h4>
  <p>Ph: +61455012874</p>
  <p style="line-height:18px;margin-top:4px">Email:<br>info@tidewatermotionbodywork.com</p>
</div>
<div class="abs foot-divider" style="left:810px"></div>
<div class="abs foot-col" style="left:852px">
  <h4>Business Hours</h4>
  <div class="hours">
    <span>Mon</span><span>09:00 - 18:00</span>
    <span>Tue</span><span>09:00 - 17:00</span>
    <span>Wed</span><span>09:00 - 18:00</span>
    <span>Thu</span><span>09:00 - 17:00</span>
    <span>Fri</span><span>09:00 - 18:00</span>
    <span>Sat</span><span>09:00 - 17:00</span>
    <span>Sun</span><span>10:00 - 17:00</span>
  </div>
</div>
<svg class="abs footer-strip" width="1200" height="80" viewBox="0 0 1200 80" aria-hidden="true">
  <polygon points="0,29 1200,0 1200,80 0,80" fill="var(--blue-light)"/>
</svg>
<p class="abs copyright">Copyright © 2015 Tidewater Motion Bodywork.All Right Reserved &nbsp;|&nbsp; Term of Services</p>
<div class="abs social" aria-label="Social links"><span></span><span></span><span></span><span></span><span></span></div>

</body>
</html>
```